Oil Field Service company needs professional business cards

Looking to clean up our current company business cards and look a little more professional. Brenwick Casing Services is a US based company that services the oil field. We deal with engineers, managers and oil rigs....................................................................................................................................................................................................................................................................................................................................................................................................

Target Market(s)

Oil and Gas professionals

Industry/Entity Type

Oil And Gas

Contact Information for Business Card

See attached photo as example

Font styles to use
Sans Serif

Colors
ec1f27

Requirements
Must have
• Company Logo, Name, Title, Cell, Office, Fax, Email.
• See attached photo
Nice to have
• External CRT, Internal CRT, Casing Crews, Torque Turn, Laydown Machine
Should not have
• Do not introduce any new pictures and keep it professional looking

```html
<!DOCTYPE html>
<html lang="en">
<head>
<meta charset="utf-8">
<title>Brenwick Casing Services – Business Card</title>
<link rel="stylesheet" href="https://fonts.googleapis.com/css2?family=Montserrat:wght@700&family=Open+Sans:ital,wght@0,400;0,600;1,400&display=swap">
<style>
  :root {
    --brand-red: #ec1f27;
    --deep-red: #c8151c;
    --slate: #4a545e;
    --slate-dark: #3b434b;
    --slate-light: #66717b;
    --white: #ffffff;
    --paper: #ececec;
  }
  * { box-sizing: border-box; margin: 0; padding: 0; }
  html, body {
    width: 1200px; height: 950px; overflow: hidden;
    background: var(--paper);
    font-family: "Open Sans", Arial, sans-serif;
  }
  .sheet { position: relative; width: 1200px; height: 950px; }
  .card {
    position: absolute; left: 250px; width: 700px; height: 400px;
    overflow: hidden; box-shadow: 0 6px 18px rgba(0,0,0,.18);
  }
  .card--front { top: 50px; background: linear-gradient(100deg, var(--slate-light), var(--slate) 45%, var(--slate-dark)); }
  .card--back { top: 500px; background: var(--brand-red); }

  .front-bands { position: absolute; inset: 0; }

  .wordmark { color: var(--white); font-family: "Montserrat", Arial, sans-serif; font-weight: 700; text-transform: uppercase; text-align: center; line-height: 1; }
  .wordmark__main { display: block; font-size: 52px; letter-spacing: 1px; }
  .wordmark__sub { display: block; font-size: 15px; letter-spacing: 4px; margin-top: 8px; }

  .card--front .wordmark { position: absolute; left: 40px; top: 165px; width: 300px; }
  .divider { position: absolute; left: 360px; top: 70px; width: 1px; height: 260px; background: rgba(255,255,255,.35); }

  .contact { position: absolute; left: 390px; top: 80px; color: var(--white); }
  .contact__name { color: var(--brand-red); font-size: 26px; font-weight: 600; }
  .contact__title, .contact__city { font-size: 15px; line-height: 1.5; }
  .contact__title { margin-top: 2px; }
  .contact__list { list-style: none; margin-top: 12px; }
  .contact__item { display: flex; align-items: center; gap: 10px; font-size: 15px; line-height: 1.65; }
  .contact__icon { width: 14px; height: 14px; flex: none; }
  .contact__web { font-size: 15px; margin-top: 8px; }

  .card--back .wordmark { position: absolute; left: 0; right: 0; top: 110px; }
  .card--back .wordmark__main { font-size: 76px; }
  .card--back .wordmark__sub { font-size: 20px; letter-spacing: 6px; margin-top: 12px; }
  .services { position: absolute; left: 0; right: 0; top: 270px; text-align: center; color: var(--white); font-style: italic; font-size: 17px; line-height: 1.6; }
</style>
</head>
<body>
<main class="sheet">
  <section class="card card--front" aria-label="Business card front">
    <svg class="front-bands" viewBox="0 0 700 400" preserveAspectRatio="none" aria-hidden="true">
      <path d="M0 0 H700 V18 C520 10 330 10 0 48 Z" fill="var(--brand-red)"/>
      <path d="M0 0 H260 C150 10 60 22 0 34 Z" fill="var(--deep-red)"/>
      <path d="M0 400 H700 V374 C500 392 280 392 0 360 Z" fill="var(--brand-red)"/>
      <path d="M700 400 H430 C560 392 640 384 700 374 Z" fill="var(--deep-red)"/>
    </svg>
    <div class="wordmark">
      <span class="wordmark__main">Brenwick</span>
      <span class="wordmark__sub">Casing Services</span>
    </div>
    <div class="divider"></div>
    <div class="contact">
      <p class="contact__name">Cole Harlan</p>
      <p class="contact__title">Area Manager</p>
      <p class="contact__city">Elkford, OK 73899</p>
      <ul class="contact__list">
        <li class="contact__item">
          <svg class="contact__icon" viewBox="0 0 16 16" aria-label="Office"><path d="M3 1 L6 1 L7 5 L5 6.5 C6 9 7 10 9.5 11 L11 9 L15 10 L15 13 C15 14 14 15 13 15 C6 15 1 10 1 3 C1 2 2 1 3 1 Z" fill="var(--brand-red)"/></svg>
          (580)555-0140
        </li>
        <li class="contact__item">
          <svg class="contact__icon" viewBox="0 0 16 16" aria-label="Cell"><rect x="4" y="1" width="8" height="14" rx="1.5" fill="none" stroke="var(--brand-red)" stroke-width="1.6"/><circle cx="8" cy="12.5" r="0.9" fill="var(--brand-red)"/></svg>
          (580)555-0172
        </li>
        <li class="contact__item">
          <svg class="contact__icon" viewBox="0 0 16 16" aria-label="Fax"><rect x="1" y="6" width="14" height="8" rx="1" fill="var(--brand-red)"/><rect x="4" y="1" width="8" height="6" fill="var(--brand-red)"/></svg>
          (580)555-0195
        </li>
        <li class="contact__item">
          <svg class="contact__icon" viewBox="0 0 16 16" aria-label="Email"><rect x="1" y="3" width="14" height="10" rx="1" fill="var(--brand-red)"/><path d="M1.5 3.8 L8 9 L14.5 3.8" fill="none" stroke="var(--slate)" stroke-width="1.2"/></svg>
          cole@brenwick.com
        </li>
      </ul>
      <p class="contact__web">www.brenwick.com</p>
    </div>
  </section>

  <section class="card card--back" aria-label="Business card back">
    <div class="wordmark">
      <span class="wordmark__main">Brenwick</span>
      <span class="wordmark__sub">Casing Services</span>
    </div>
    <p class="services">External CRT | Internal CRT | Casing Crews<br>Torque Turn | Laydown Machine</p>
  </section>
</main>
</body>
</html>
```